Residential Remodeling Contractor needs updated business card

I need a new design for my business card.
Name of the company is Ridgefell Construction. I need a card that commands presence, strength, integrity. I have been in business for 28 years. I am a Residential Remodeling Contractor that covers all aspects of a residential remodel and build.

```html
<!DOCTYPE html>
<html lang="en">
<head>
<meta charset="utf-8">
<title>Ridgefell Construction – Business Card</title>
<link rel="stylesheet" href="https://fonts.googleapis.com/css2?family=Cinzel:wght@500;600&family=Poppins:ital,wght@0,400;0,500;1,400&display=swap">
<style>
  :root {
    --stage: #9b9b9b;
    --card-navy: #1f3d7e;
    --ink-light: #ffffff;
    --rule: rgba(255, 255, 255, 0.35);
  }
  * { box-sizing: border-box; margin: 0; padding: 0; }
  html, body { width: 1093px; height: 1200px; overflow: hidden; }
  body { background: var(--stage); position: relative; font-family: "Poppins", sans-serif; color: var(--ink-light); }

  .card {
    position: absolute;
    left: 265px;
    width: 580px;
    height: 356px;
    border-radius: 26px;
    background: var(--card-navy);
    overflow: hidden;
  }
  .card--front { top: 226px; }
  .card--back { top: 621px; }

  .wordmark {
    position: absolute;
    font-family: "Cinzel", serif;
    font-weight: 600;
    line-height: 1;
    color: var(--ink-light);
    white-space: nowrap;
  }
  .wordmark span { display: block; }
  .card--front .wordmark { left: 80px; top: 160px; font-size: 23px; }
  .card--back .wordmark { left: 147px; top: 170px; font-size: 36px; }

  .divider {
    position: absolute;
    left: 288px; top: 74px;
    width: 1px; height: 208px;
    background: var(--rule);
  }

  .contact { position: absolute; left: 306px; top: 90px; }
  .contact__name {
    font-family: "Cinzel", serif;
    font-weight: 600;
    font-size: 21px;
    line-height: 1;
    white-space: nowrap;
  }
  .contact__role { font-size: 16px; line-height: 1.1; margin-top: 1px; }
  .contact__list { list-style: none; margin-top: 12px; }
  .contact__list li {
    display: flex; align-items: center; gap: 7px;
    font-size: 16.5px; line-height: 21px; white-space: nowrap;
  }
  .contact__list svg { width: 15px; height: 15px; flex: none; }
  .contact__address { font-size: 16.5px; line-height: 21px; margin-top: 13px; padding-left: 1px; white-space: nowrap; }

  .tagline { position: absolute; left: 148px; top: 290px; font-size: 14.8px; line-height: 19px; white-space: nowrap; }
  .tagline__since { font-style: italic; }
  .tagline__trade { font-weight: 500; letter-spacing: 0.01em; }
</style>
</head>
<body>

<section class="card card--front" aria-label="Business card front">
  <h1 class="wordmark"><span>Ridgefell</span><span>Construction</span></h1>
  <div class="divider"></div>
  <div class="contact">
    <p class="contact__name">Daniel Whitmore</p>
    <p class="contact__role">Managing Director</p>
    <ul class="contact__list">
      <li>
        <svg viewBox="0 0 16 16" aria-hidden="true"><path fill="#fff" d="M3.2 1.5l2.3 2.4-1.2 1.6c.9 2 2.3 3.4 4.3 4.3l1.6-1.2 2.4 2.3-1.3 2.1C6.6 12.7 3.3 9.4 1.1 2.8z"/></svg>
        044-730 218 564
      </li>
      <li>
        <svg viewBox="0 0 16 16" aria-hidden="true"><rect x="1" y="3.5" width="14" height="9" fill="none" stroke="#fff" stroke-width="1.4"/><path d="M1 3.5l7 5.5 7-5.5" fill="none" stroke="#fff" stroke-width="1.4"/></svg>
        info@ridgefellbuild.com
      </li>
      <li>
        <svg viewBox="0 0 16 16" aria-hidden="true"><g fill="none" stroke="#fff" stroke-width="1.2"><circle cx="8" cy="8" r="6.5"/><ellipse cx="8" cy="8" rx="2.8" ry="6.5"/><path d="M1.5 8h13M2.5 4.8h11M2.5 11.2h11"/></g></svg>
        www.ridgefellbuild.com
      </li>
    </ul>
    <p class="contact__address">421, Address line goes here<br>45452,Country Name</p>
  </div>
</section>

<section class="card card--back" aria-label="Business card back">
  <h2 class="wordmark"><span>Ridgefell</span><span>Construction</span></h2>
  <div class="tagline">
    <p class="tagline__since">Since 28 years</p>
    <p class="tagline__trade">RESIDENTIAL CONTRACTOR FOR REMODELING AND BUILD</p>
  </div>
</section>

</body>
</html>
```